Redesign website for small print company

Vindurgata is a small printing company in Iceland mainly servicing Students, schools, etc. We are also doing all kind of other jobs, like business cards, book printing, brochure printing etc. We are also selling books online.
Our website is: www.vindurgata.is
What we are looking for is:
- Web Design (Uncoded - PSD layout only)
- Mobile friendly design, using our current color scheme: Red, green, yellow and light gray.
- Clean simple design
- Simple, light and easy to use.
- More menu Items/drop down
Industry/Entity Type
Digital Printing
Number of Pages Required
5+ page
Requirements
Must have
- Easy navigation
- Designed for mobile
- Current color scheme (see logo)
Nice to have
- Icon based products

```html
<!DOCTYPE html>
<html lang="en">
<head>
<meta charset="utf-8">
<title>Vindurgata – Printing for students and schools</title>
<link href="https://fonts.googleapis.com/css2?family=Lato:wght@400;700;900&display=swap" rel="stylesheet">
<style>
:root{
  --red:#c0282a;
  --green:#2f5a2b;
  --yellow:#eac722;
  --gray:#7e7e7e;
  --about:#2f9a60;
  --about-frame:#5cb487;
  --footer:#1e1c1d;
  --ink:#222;
  --muted:#777;
  --line:#e2e2e2;
}
*{box-sizing:border-box;margin:0;padding:0}
html,body{width:1200px;height:2913px;overflow:hidden;background:#fff}
body{font-family:'Lato',sans-serif;color:var(--ink);position:relative}

/* header */
.site-header{position:absolute;left:0;top:0;width:1200px;height:138px;background:#fff;z-index:3}
.brand{position:absolute;left:103px;top:0;width:190px;height:198px;background:#fff;box-shadow:0 2px 8px rgba(0,0,0,.18);display:flex;flex-direction:column;align-items:center;justify-content:center;gap:14px;z-index:4}
.brand-mark{width:70px;height:70px;background:var(--red);border-radius:50%}
.brand-name{font-weight:900;font-size:20px;color:var(--ink);letter-spacing:.5px}
.contact-strip{position:absolute;top:20px;left:545px;display:flex;gap:26px;font-size:17px;color:#444}
.contact-item{display:flex;align-items:center;gap:10px}
.contact-icon{width:36px;height:36px;border-radius:50%;display:flex;align-items:center;justify-content:center;border:2px solid}
.main-nav{position:absolute;top:82px;left:372px;display:flex;font-size:15px;font-weight:700;color:#333}
.main-nav a{text-decoration:none;color:inherit;padding:0 20px}
.main-nav a.active{color:var(--red)}
.lang{position:absolute;left:936px;top:78px;width:86px;height:29px;border:1px solid var(--about);color:var(--green);font-size:14px;display:flex;align-items:center;justify-content:center;gap:6px}
.header-tools{position:absolute;left:1043px;top:80px;display:flex;gap:16px}

/* dropdown */
.dropdown{position:absolute;left:355px;top:138px;width:529px;height:128px;background:var(--red);z-index:5;display:grid;grid-template-columns:170px 164px 160px;padding:22px 0 0 32px;row-gap:9px;color:#fff;font-size:14px}
.dropdown span::before{content:"";display:inline-block;border-left:6px solid #fff;border-top:4px solid transparent;border-bottom:4px solid transparent;margin-right:12px}
.dropdown-caret{position:absolute;left:592px;top:128px;border-left:10px solid transparent;border-right:10px solid transparent;border-bottom:10px solid var(--red);z-index:5}

/* hero */
.hero{position:absolute;left:0;top:138px;width:1200px;height:610px;background:linear-gradient(160deg,#6e6a62 0%,#4a4743 45%,#2f2d2b 100%)}
.hero-title{position:absolute;left:0;top:185px;width:1200px;text-align:center;font-size:96px;font-weight:900;color:#fff;letter-spacing:1px;line-height:1}
.hero-text{position:absolute;left:240px;top:290px;width:720px;text-align:center;font-size:15px;line-height:24px;color:#fff;font-weight:700}
.hero-arrow{position:absolute;top:268px}
.hero-curve{position:absolute;left:0;bottom:0;width:1200px;height:80px}

/* products */
.section-title{position:absolute;left:0;width:1200px;text-align:center;font-size:35px;font-weight:900;color:var(--ink)}
.toolbar{position:absolute;left:101px;top:826px;width:998px;height:60px;border-top:1px solid var(--line);border-bottom:1px solid var(--line)}
.toolbar .count{position:absolute;left:25px;top:19px;font-size:13px;color:var(--muted)}
.toolbar .order{position:absolute;right:25px;top:16px;width:85px;height:26px;border:1px solid #ccc;font-size:13px;color:var(--muted);display:flex;align-items:center;justify-content:center;gap:6px}
.pager{position:absolute;left:1006px;top:896px;display:flex;gap:8px;align-items:center;font-size:12px;color:var(--muted)}
.pager b{width:22px;height:22px;border:1px solid #ccc;display:inline-block}
.product{position:absolute;width:229px;height:218px;color:#fff;text-align:center}
.product .icon{width:74px;height:74px;border-radius:50%;background:#fff;margin:18px auto 0;display:flex;align-items:center;justify-content:center}
.product h3{font-size:13px;font-weight:900;margin-top:16px;letter-spacing:.3px}
.product p{font-size:12px;line-height:19.5px;margin:10px auto 0;width:190px}
.red{background:var(--red)}.green{background:var(--green)}.yellow{background:var(--yellow)}.gray{background:var(--gray)}
.btn-all{position:absolute;left:472px;top:1450px;width:258px;height:51px;border-radius:26px;background:var(--footer);color:#fff;font-size:15px;font-weight:900;display:flex;align-items:center;justify-content:center;gap:12px;letter-spacing:.3px}

/* about */
.about{position:absolute;left:0;top:1604px;width:1200px;height:598px;background:var(--about);color:#fff}
.about h2{position:absolute;left:0;top:62px;width:1200px;text-align:center;font-size:35px;font-weight:900}
.about h3{position:absolute;left:101px;top:143px;font-size:30px;font-weight:900}
.about .copy{position:absolute;left:101px;top:206px;width:500px;font-size:13px;line-height:23px}
.about .copy p{margin-bottom:24px}
.about-frame{position:absolute;left:649px;top:142px;width:437px;height:363px;background:var(--about-frame);padding:12px}
.about-photo{width:100%;height:100%;background:linear-gradient(180deg,var(--yellow) 0%,var(--yellow) 40%,#b9b4ab 62%,#6f6a66 100%)}

/* map */
.map{position:absolute;left:0;top:2202px;width:1200px;height:344px;background:linear-gradient(90deg,#a8cbe6 0%,#b7d3ea 45%,#e6e4df 60%,#eeece8 100%)}

/* footer */
.site-footer{position:absolute;left:0;top:2546px;width:1200px;height:367px;background:var(--footer);color:#fff}
.site-footer h4{position:absolute;top:62px;font-size:19px;font-weight:900;letter-spacing:.3px}
.links{position:absolute;top:98px;list-style:none;font-size:15px;line-height:29px}
.links li{display:flex;align-items:center;gap:8px}
.dot{width:10px;height:10px;border-radius:50%;background:#fff;display:inline-block}
.contact-list{position:absolute;left:911px;top:98px;font-size:15px;line-height:29px}
.contact-list .row{display:flex;gap:14px;align-items:flex-start}
.footer-rule{position:absolute;left:99px;top:283px;width:1002px;height:1px;background:#3a3839}
.copyright{position:absolute;left:99px;top:310px;font-size:12px;color:#ccc}
.pay{position:absolute;top:308px;width:36px;height:20px;border-radius:3px;background:#8a8a8a}
.version{position:absolute;left:1136px;top:310px;font-size:12px;color:#aaa}
</style>
</head>
<body>

<header class="site-header">
  <div class="brand">
    <span class="brand-mark"></span>
    <span class="brand-name">VINDURGATA</span>
  </div>
  <div class="contact-strip">
    <div class="contact-item">
      <span class="contact-icon" style="border-color:var(--green)"><svg width="16" height="16" viewBox="0 0 24 24"><path fill="#2f5a2b" d="M6.6 10.8a15 15 0 0 0 6.6 6.6l2.2-2.2c.3-.3.7-.4 1-.2 1.1.4 2.3.6 3.6.6.6 0 1 .4 1 1V20c0 .6-.4 1-1 1A17 17 0 0 1 3 4c0-.6.4-1 1-1h3.5c.6 0 1 .4 1 1 0 1.3.2 2.5.6 3.6.1.3 0 .7-.2 1z"/></svg></span>555 0142
    </div>
    <div class="contact-item">
      <span class="contact-icon" style="border-color:var(--red);background:var(--red)"><svg width="16" height="12" viewBox="0 0 16 12"><rect width="16" height="12" rx="1" fill="#fff"/><path d="M0 1l8 6 8-6" stroke="#c0282a" stroke-width="1.6" fill="none"/></svg></span>verk@vindurgata.is
    </div>
    <div class="contact-item">
      <span class="contact-icon" style="border-color:var(--yellow)"><svg width="18" height="18" viewBox="0 0 20 20"><circle cx="10" cy="10" r="8" fill="none" stroke="#eac722" stroke-width="2"/><path d="M10 5v5l3 2" stroke="#eac722" stroke-width="2" fill="none"/></svg></span>Mon - Fri: 9-17
    </div>
  </div>
  <nav class="main-nav">
    <a class="active">HOME</a><a>ABOUT US</a><a>PRODUCTS</a><a>SERVICES</a><a>CONTACT US</a>
  </nav>
  <div class="lang">English <svg width="9" height="6" viewBox="0 0 9 6"><path d="M1 1l3.5 3.5L8 1" stroke="#2f5a2b" stroke-width="1.5" fill="none"/></svg></div>
  <div class="header-tools">
    <svg width="22" height="22" viewBox="0 0 22 22"><circle cx="9" cy="9" r="7" fill="none" stroke="#bbb" stroke-width="2"/><path d="M14 14l6 6" stroke="#bbb" stroke-width="2"/></svg>
    <svg width="22" height="22" viewBox="0 0 22 22"><rect x="3" y="7" width="16" height="14" fill="none" stroke="#bbb" stroke-width="2"/><path d="M7 7V5a4 4 0 0 1 8 0v2" fill="none" stroke="#bbb" stroke-width="2"/></svg>
  </div>
</header>

<div class="dropdown-caret"></div>
<div class="dropdown">
  <span>Essays</span><span>Bookprinting</span><span>Brochure Printing</span>
  <span>Business cards</span><span>Posters</span><span>Calendar 2018</span>
  <span>Leaflets</span><span>Textbooks</span>
</div>

<section class="hero" role="img" aria-label="Photo of hands working over printed sheets and colour swatches on a table">
  <svg class="hero-arrow" style="left:36px" width="18" height="32" viewBox="0 0 18 32"><path d="M16 2L2 16l14 14" stroke="#fff" stroke-opacity=".7" stroke-width="2" fill="none"/></svg>
  <svg class="hero-arrow" style="left:1136px" width="18" height="32" viewBox="0 0 18 32"><path d="M2 2l14 14L2 30" stroke="#fff" stroke-opacity=".7" stroke-width="2" fill="none"/></svg>
  <div class="hero-title">VINDURGATA</div>
  <p class="hero-text">Quis autem vel eum iure reprehenderit qui in ea voluptate velit esse quam nihil molestiae consequatur, vel illum qui dolorem eum fugiat quo voluptas nulla.</p>
  <svg class="hero-curve" viewBox="0 0 1200 80" preserveAspectRatio="none"><path d="M0 80 Q600 -40 1200 80 Z" fill="#fff"/></svg>
</section>

<h2 class="section-title" style="top:770px">OUR PRODUCTS</h2>
<div class="toolbar">
  <span class="count">8 Products</span>
  <span class="order">Order <svg width="8" height="5" viewBox="0 0 8 5"><path d="M1 1l3 3 3-3" stroke="#888" fill="none"/></svg></span>
</div>
<div class="pager"><b></b>Page<b></b></div>

<div class="product red" style="left:101px;top:932px">
  <div class="icon"><svg width="30" height="30" viewBox="0 0 30 30"><rect x="5" y="5" width="20" height="20" fill="none" stroke="#c0282a" stroke-width="2"/><path d="M9 11h12M9 15h12M9 19h8" stroke="#c0282a" stroke-width="2"/></svg></div>
  <h3>PHOTOCOPYING</h3><p>Lorem ipsum dolor sit amet, consect adipiscing elit, sed do eiusmod tempor incididunt.</p>
</div>
<div class="product green" style="left:357px;top:932px">
  <div class="icon"><svg width="30" height="30" viewBox="0 0 30 30"><path d="M15 3v18M11 21h8l-4 6z" stroke="#2f5a2b" stroke-width="2" fill="none"/><rect x="11" y="7" width="8" height="14" fill="none" stroke="#2f5a2b" stroke-width="2"/></svg></div>
  <h3>CREATIVE PROCESS</h3><p>Lorem ipsum dolor sit amet, consect adipiscing elit, sed do eiusmod tempor incididunt.</p>
</div>
<div class="product yellow" style="left:613px;top:932px">
  <div class="icon"><svg width="30" height="30" viewBox="0 0 30 30"><path d="M4 18l12-12 10 10-12 8z" fill="#eac722"/><path d="M4 22h22" stroke="#eac722" stroke-width="2"/></svg></div>
  <h3>SCANNING</h3><p>Lorem ipsum dolor sit amet, consect adipiscing elit, sed do eiusmod tempor incididunt.</p>
</div>
<div class="product gray" style="left:869px;top:932px">
  <div class="icon"><svg width="30" height="30" viewBox="0 0 30 30"><rect x="8" y="4" width="14" height="8" fill="none" stroke="#7e7e7e" stroke-width="2"/><rect x="4" y="12" width="22" height="10" fill="#7e7e7e"/><rect x="8" y="20" width="14" height="6" fill="#fff" stroke="#7e7e7e" stroke-width="2"/></svg></div>
  <h3>DIGITAL PRINTING</h3><p>Lorem ipsum dolor sit amet, consect adipiscing elit, sed do eiusmod tempor incididunt.</p>
</div>
<div class="product gray" style="left:101px;top:1190px">
  <div class="icon"><svg width="30" height="30" viewBox="0 0 30 30"><rect x="3" y="7" width="24" height="16" rx="2" fill="none" stroke="#7e7e7e" stroke-width="2"/><rect x="7" y="11" width="6" height="6" fill="#7e7e7e"/><path d="M16 12h7M16 16h7" stroke="#7e7e7e" stroke-width="2"/></svg></div>
  <h3>BUSINESS CARDS</h3><p>Lorem ipsum dolor sit amet, consect adipiscing elit, sed do eiusmod tempor incididunt.</p>
</div>
<div class="product yellow" style="left:357px;top:1190px">
  <div class="icon"><svg width="30" height="30" viewBox="0 0 30 30"><path d="M3 7h10l2 2 2-2h10v16H17l-2 2-2-2H3z" fill="none" stroke="#eac722" stroke-width="2"/><path d="M15 9v16" stroke="#eac722" stroke-width="2"/></svg></div>
  <h3>TOURIST BROCHURE</h3><p>Lorem ipsum dolor sit amet, consect adipiscing elit, sed do eiusmod tempor incididunt.</p>
</div>
<div class="product green" style="left:613px;top:1190px">
  <div class="icon"><svg width="30" height="30" viewBox="0 0 30 30"><path d="M4 12l11-6 11 6-11 6z" fill="#2f5a2b"/><path d="M4 16l11 6 11-6M4 20l11 6 11-6" stroke="#2f5a2b" stroke-width="2" fill="none"/></svg></div>
  <h3>TEXTBOOKS</h3><p>Lorem ipsum dolor sit amet, consect adipiscing elit, sed do eiusmod tempor incididunt.</p>
</div>
<div class="product red" style="left:869px;top:1190px">
  <div class="icon"><svg width="30" height="30" viewBox="0 0 30 30"><rect x="7" y="3" width="16" height="24" fill="none" stroke="#c0282a" stroke-width="2"/><path d="M11 21v-4M15 21v-8M19 21v-6" stroke="#c0282a" stroke-width="2"/></svg></div>
  <h3>REPORTS</h3><p>Lorem ipsum dolor sit amet, consect adipiscing elit, sed do eiusmod tempor incididunt.</p>
</div>

<div class="btn-all">VIEW ALL PRODUCTS <svg width="16" height="16" viewBox="0 0 16 16"><circle cx="8" cy="8" r="8" fill="#fff"/><path d="M5 8h6M8 5l3 3-3 3" stroke="#1e1c1d" stroke-width="1.8" fill="none"/></svg></div>

<section class="about">
  <h2>ABOUT US</h2>
  <h3>Welcome to University</h3>
  <div class="copy">
    <p>University education is a company located in the campus, which has specialized in the service of school staff, as well as providing general public printing.</p>
    <p>Higher education publishes seminars and first-class textbooks for courses, prints theses for lesson, as well as working on an unprecedented number of smaller pieces for students, teachers and organizations. These include brochures, reports, questionnaires, business cards, books, OCR scanning and more.</p>
    <p>Higher education is a tailored print shop, The Puffin is the official eco-label of the Nordic countries, which has created a foothold in this country and is known among consumers.</p>
    <p>University education is located at the corner of Hrafnagata and Norðurgata. (walked into Norðurgötumegin)</p>
  </div>
  <div class="about-frame">
    <div class="about-photo" role="img" aria-label="Photo of a hand drawing with a pen beside colour swatches, on a yellow background"></div>
  </div>
</section>

<div class="map" role="img" aria-label="Street map showing the shop location near the campus by the coast"></div>

<footer class="site-footer">
  <h4 style="left:99px">COMPANY</h4>
  <ul class="links" style="left:99px"><li>Home</li><li>About Us</li><li>Products</li><li>Services</li><li>Contact Us</li></ul>
  <ul class="links" style="left:330px"><li>Terms of Use</li><li>Privacy Policy</li><li>Site Map</li></ul>
  <h4 style="left:612px">SOCIAL MEDIA</h4>
  <ul class="links" style="left:612px"><li><span class="dot"></span>Facepage</li><li><span class="dot"></span>Chirper</li><li><span class="dot"></span>WorkLink</li></ul>
  <h4 style="left:911px">CONTACT US</h4>
  <div class="contact-list">
    <div class="row"><svg width="14" height="20" viewBox="0 0 14 20" style="margin-top:5px"><path d="M7 0a7 7 0 0 0-7 7c0 5 7 13 7 13s7-8 7-13a7 7 0 0 0-7-7z" fill="#fff"/><circle cx="7" cy="7" r="2.5" fill="#1e1c1d"/></svg><div>vindurgata.is,<br>Vindbær, IS 104</div></div>
    <div class="row" style="margin-top:29px"><svg width="16" height="16" viewBox="0 0 24 24" style="margin-top:6px"><path fill="#fff" d="M6.6 10.8a15 15 0 0 0 6.6 6.6l2.2-2.2c.3-.3.7-.4 1-.2 1.1.4 2.3.6 3.6.6.6 0 1 .4 1 1V20c0 .6-.4 1-1 1A17 17 0 0 1 3 4c0-.6.4-1 1-1h3.5c.6 0 1 .4 1 1 0 1.3.2 2.5.6 3.6.1.3 0 .7-.2 1z"/></svg>555 0142</div>
    <div class="row"><svg width="18" height="13" viewBox="0 0 16 12" style="margin-top:8px"><rect width="16" height="12" fill="#fff"/><path d="M0 1l8 6 8-6" stroke="#1e1c1d" stroke-width="1.4" fill="none"/></svg>verk@vindurgata.is</div>
  </div>
  <div class="footer-rule"></div>
  <div class="copyright">© 2018 VINDURGATA. All right reserved Term of Use</div>
  <span class="pay" style="left:1024px"></span>
  <span class="pay" style="left:1066px"></span>
  <div class="version">C16</div>
</footer>

</body>
</html>
```